New Template, new corporate image Kelvoran 2022

New template designs for google slides or PowerPoint. Match to new corporate image. The new website www.kelvoran-mx.example Needs to match our new version. Technology and Artificial Intelligence elements to reflect our type of work.
We are adding old version of template and will send elements for the new corporate images.
Please consider our website as the main corporate image.
Our templates are being used on customer presentations, webminars, internal work only.
We have our main name of company Kelvoran. Kelvoran has to be in all the templates.
Secondary logo or branded service is: Vastrelim.

Target Market(s)

Industrial users. Asset managers. Corporate visitors and customers.

Industry/Entity Type

Automotive. Chemical. Food and Beverage. Manufacturing

Other font styles liked:
• GE INSPIRA. RALEWAY

Colors
0054AA
0677BA
7BADD7
CADEEF
E8F1F8

Requirements
Must have
• Match to our elements on the new image. Use Brain Icons. Chips icons to connect equipments with software and control. Innovation.
Nice to have
• Unique images, machine images. Connecting machines and data elements. Template version for google slides. Image for industrial software for control equipment and saving money to manufacturers. Segments: Automotive, Chemical, Food and Beverages, Mining and pharmaceutical, Energy Management
Should not have
• old elements. not to much images of medical devices. Do not seems like a hospital.

```html
<!DOCTYPE html>
<html lang="en">
<head>
<meta charset="utf-8">
<title>Kelvoran Presentation Template – Part 1</title>
<link href="https://fonts.googleapis.com/css2?family=Montserrat:wght@400;500;600;700&family=Arimo:wght@700&display=swap" rel="stylesheet">
<style>
  :root{
    --board:#e6e5e3;
    --ink:#111111;
    --black:#050608;
    --footer:#262626;
    --brand-blue:#0054AA;
    --mid-blue:#0677BA;
    --sky:#1fa2e0;
    --light-blue:#7BADD7;
    --white:#ffffff;
    --body:#2a2a2a;
  }
  *{box-sizing:border-box;margin:0;padding:0}
  html,body{width:1200px;height:1200px;overflow:hidden;background:var(--board)}
  body{position:relative;font-family:"Montserrat",Arial,sans-serif;color:var(--body)}

  .slide{position:absolute;width:534px;height:300px;overflow:hidden;background:var(--white)}
  .slide--cover-1{left:53px;top:46px;background:var(--black)}
  .slide--cover-2{left:614px;top:46px;background:#0a2f55}
  .slide--break{left:53px;top:374px;background:var(--black)}
  .slide--content{left:614px;top:374px}
  .slide--agenda{left:53px;top:700px}
  .slide--mission{left:614px;top:700px}

  .layer{position:absolute;inset:0;width:100%;height:100%}

  .wordmark{position:absolute;font-weight:600;color:var(--white);letter-spacing:.02em}
  .cover .wordmark{font-size:15px}

  .cover-title{position:absolute;font-weight:700;color:var(--white);font-size:30px;line-height:1;white-space:nowrap}
  .cover-rule{position:absolute;height:2px;width:46px;background:var(--white)}
  .cover-subtitle{position:absolute;font-weight:700;font-size:12.5px;white-space:nowrap}
  .cover-date{position:absolute;font-size:7.5px;color:var(--white)}

  .slide--cover-1 .wordmark{left:23px;top:34px}
  .slide--cover-1 .cover-title{left:21px;top:115px}
  .slide--cover-1 .cover-rule{left:22px;top:162px}
  .slide--cover-1 .cover-subtitle{left:22px;top:176px;color:var(--sky)}
  .slide--cover-1 .cover-date{left:22px;top:196px}

  .slide--cover-2 .wordmark{left:37px;top:42px}
  .slide--cover-2 .cover-title{left:34px;top:102px}
  .slide--cover-2 .cover-rule{left:35px;top:148px}
  .slide--cover-2 .cover-subtitle{left:35px;top:163px;color:var(--white)}
  .slide--cover-2 .cover-date{left:35px;top:182px}

  .break-title{position:absolute;right:26px;top:112px;font-weight:700;font-size:31px;color:var(--white);line-height:1}
  .break-rule{position:absolute;right:26px;top:159px;width:47px;height:2px;background:var(--sky)}
  .break-text{position:absolute;right:26px;top:173px;font-size:8.2px;color:var(--white)}

  .slide-title{position:absolute;left:22px;top:24px;font-weight:700;font-size:19px;color:var(--brand-blue)}

  .bullets{position:absolute;left:21px;top:64px;width:490px;list-style:none}
  .bullets > li{position:relative;padding-left:9px;font-size:10.6px;line-height:13.4px;color:var(--ink)}
  .bullets > li::before{content:"•";position:absolute;left:0;color:var(--mid-blue)}
  .bullets ul{list-style:none;margin-top:5px}
  .bullets ul li{position:relative;padding-left:8px;font-size:9.6px;line-height:12px}
  .bullets ul li::before{content:"-";position:absolute;left:0;color:var(--light-blue)}

  .footer{position:absolute;left:0;bottom:0;width:100%;height:22px}
  .footer-text{position:absolute;left:22px;top:7px;font-size:5.8px;color:var(--white);white-space:nowrap}
  .footer-text .page{color:var(--sky);font-weight:600;margin-right:4px}
  .footer-text .sep{margin-right:5px}
  .footer .wordmark{left:458px;top:5px;font-size:9px;color:var(--mid-blue)}

  .agenda-divider{position:absolute;left:267px;top:66px;width:1px;height:190px;background:#d9d9d9}
  .agenda-item{position:absolute;width:200px;height:40px}
  .agenda-num{position:absolute;left:0;top:0;font-weight:700;font-size:25px;line-height:40px;color:var(--brand-blue)}
  .agenda-head{position:absolute;left:46px;top:4px;font-weight:700;font-size:9px;color:var(--brand-blue)}
  .agenda-copy{position:absolute;left:46px;top:17px;width:160px;font-size:6.6px;line-height:7.8px;color:var(--body)}

  .mission-image{position:absolute;left:0;top:56px;width:245px;height:213px}
  .mission-copy{position:absolute;left:267px;top:64px;width:250px;font-size:8.6px;line-height:10.7px;color:var(--body)}
  .mission-head{position:absolute;left:267px;top:166px;font-weight:700;font-size:10.8px;color:var(--brand-blue)}
  .mission-copy--second{top:183px}

  .part-label{position:absolute;left:55px;top:1046px;font-family:"Arimo",Arial,sans-serif;font-weight:700;font-size:107px;line-height:1;color:var(--ink);letter-spacing:-1px}
</style>
</head>
<body>

<!-- Cover 1 -->
<section class="slide slide--cover-1 cover">
  <svg class="layer" viewBox="0 0 534 300" preserveAspectRatio="none">
    <defs>
      <linearGradient id="cover1Photo" x1="0" y1="0" x2="1" y2="1">
        <stop offset="0" stop-color="#1d3550"/>
        <stop offset=".45" stop-color="#5f7591"/>
        <stop offset=".7" stop-color="#2c4f86"/>
        <stop offset="1" stop-color="#13243d"/>
      </linearGradient>
      <linearGradient id="cover1Fade" x1="0" y1="0" x2="1" y2="0">
        <stop offset="0" stop-color="#050608" stop-opacity=".85"/>
        <stop offset=".4" stop-color="#050608" stop-opacity="0"/>
      </linearGradient>
    </defs>
    <g role="img" aria-label="Photo: engineer using a tablet beside industrial machinery">
      <polygon points="200,0 534,0 534,300 120,300" fill="url(#cover1Photo)"/>
      <polygon points="200,0 534,0 534,300 120,300" fill="url(#cover1Fade)"/>
    </g>
    <polygon points="326,0 534,0 534,300 205,300" fill="#1a4c8c" opacity=".18"/>
    <line x1="326" y1="0" x2="205" y2="300" stroke="#2c7fd4" stroke-width="1"/>
    <line x1="190" y1="0" x2="275" y2="72" stroke="#7fb3e6" stroke-width=".7"/>
    <line x1="534" y1="140" x2="470" y2="300" stroke="#2c7fd4" stroke-width=".7"/>
  </svg>
  <div class="wordmark">Kelvoran</div>
  <h1 class="cover-title">Cover Title 1</h1>
  <div class="cover-rule"></div>
  <p class="cover-subtitle">Subtitle Goes Here</p>
  <p class="cover-date">Date: XX/XX/XX</p>
</section>

<!-- Cover 2 -->
<section class="slide slide--cover-2 cover">
  <svg class="layer" viewBox="0 0 534 300" preserveAspectRatio="none">
    <defs>
      <linearGradient id="cover2Photo" x1="0" y1="0" x2="1" y2="1">
        <stop offset="0" stop-color="#0c2038"/>
        <stop offset=".5" stop-color="#203a55"/>
        <stop offset="1" stop-color="#060a12"/>
      </linearGradient>
      <linearGradient id="cover2Panel" x1="0" y1="0" x2="1" y2="1">
        <stop offset="0" stop-color="#0a3a6d"/>
        <stop offset="1" stop-color="#0d4f8c"/>
      </linearGradient>
    </defs>
    <rect role="img" aria-label="Photo: circuit board with a glowing AI processor chip" x="0" y="0" width="534" height="300" fill="url(#cover2Photo)"/>
    <polygon points="0,0 243,0 417,300 0,300" fill="url(#cover2Panel)" opacity=".93"/>
    <line x1="38" y1="218" x2="75" y2="300" stroke="#9fc6ec" stroke-width=".8"/>
  </svg>
  <div class="wordmark">Kelvoran</div>
  <h1 class="cover-title">Cover Title 2</h1>
  <div class="cover-rule"></div>
  <p class="cover-subtitle">Subtitle Goes Here</p>
  <p class="cover-date">Date: XX/XX/XX</p>
</section>

<!-- Break -->
<section class="slide slide--break">
  <svg class="layer" viewBox="0 0 534 300" preserveAspectRatio="none">
    <defs>
      <linearGradient id="breakPhoto" x1="0" y1="0" x2="1" y2="1">
        <stop offset="0" stop-color="#a9b4c0"/>
        <stop offset=".35" stop-color="#3e5d86"/>
        <stop offset=".75" stop-color="#1c2c44"/>
        <stop offset="1" stop-color="#0b121d"/>
      </linearGradient>
      <linearGradient id="breakFade" x1="0" y1="0" x2="1" y2="0">
        <stop offset=".25" stop-color="#050608" stop-opacity="0"/>
        <stop offset=".7" stop-color="#050608" stop-opacity=".9"/>
      </linearGradient>
    </defs>
    <g role="img" aria-label="Photo: two engineers working at computers in a control room">
      <rect x="0" y="0" width="360" height="300" fill="url(#breakPhoto)"/>
      <rect x="0" y="0" width="360" height="300" fill="url(#breakFade)"/>
    </g>
    <polygon points="196,0 534,0 534,300 351,300" fill="#050608"/>
    <polygon points="196,0 240,0 360,300 351,300" fill="#0d2d55" opacity=".5"/>
    <line x1="196" y1="0" x2="351" y2="300" stroke="#2c7fd4" stroke-width="1"/>
  </svg>
  <h2 class="break-title">Break Slide</h2>
  <div class="break-rule"></div>
  <p class="break-text">Lorem ipsum dolor sit amet, consectetur.</p>
</section>

<!-- Content -->
<section class="slide slide--content">
  <h2 class="slide-title">Template Style</h2>
  <ul class="bullets">
    <li>Lorem ipsum dolor sit amet, consectetur adipiscing elit. Curabitur at fringilla velit. In ac sagittis nulla. Nulla quis erat et ligula aliquam sagittis in viverra mauris. Pellentesque pharetra hendrerit orci at.
      <ul>
        <li>Donec vel suscipit purus, ultrices ornare neque. Sed nec est a lacus lacinia venenatis non at est. Vestibulum vitae lorem lectus. Phasellus gravida mauris a sapien elementum malesuada. Vestibulum ut urna eu dolor suscipit condimentum. Curabitur sed commodo leo. Phasellus faucibus sem ante.</li>
      </ul>
    </li>
  </ul>
  <footer class="footer">
    <svg class="layer" viewBox="0 0 534 22" preserveAspectRatio="none">
      <polygon points="0,0 424,0 434,22 0,22" fill="var(--footer)"/>
      <polygon points="424,0 432,0 444,22 434,22" fill="var(--mid-blue)"/>
    </svg>
    <p class="footer-text"><span class="page">4</span><span class="sep">|</span>Copyright © Kelvoran 2022</p>
    <div class="wordmark">Kelvoran</div>
  </footer>
</section>

<!-- Agenda -->
<section class="slide slide--agenda">
  <h2 class="slide-title">Agenda Slide</h2>
  <div class="agenda-divider"></div>

  <div class="agenda-item" style="left:22px;top:71px"><span class="agenda-num">01</span><h3 class="agenda-head">Section Header</h3><p class="agenda-copy">Lorem ipsum dolor sit amet, consectetur adipiscing elit. Curabitur at fringilla velit.</p></div>
  <div class="agenda-item" style="left:21px;top:137px"><span class="agenda-num">02</span><h3 class="agenda-head">Section Header</h3><p class="agenda-copy">Lorem ipsum dolor sit amet, consectetur adipiscing elit. Curabitur at fringilla velit.</p></div>
  <div class="agenda-item" style="left:21px;top:202px"><span class="agenda-num">03</span><h3 class="agenda-head">Section Header</h3><p class="agenda-copy">Lorem ipsum dolor sit amet, consectetur adipiscing elit. Curabitur at fringilla velit.</p></div>

  <div class="agenda-item" style="left:299px;top:71px"><span class="agenda-num">04</span><h3 class="agenda-head">Section Header</h3><p class="agenda-copy">Lorem ipsum dolor sit amet, consectetur adipiscing elit. Curabitur at fringilla velit.</p></div>
  <div class="agenda-item" style="left:300px;top:137px"><span class="agenda-num">05</span><h3 class="agenda-head">Section Header</h3><p class="agenda-copy">Lorem ipsum dolor sit amet, consectetur adipiscing elit. Curabitur at fringilla velit.</p></div>
  <div class="agenda-item" style="left:300px;top:202px"><span class="agenda-num">06</span><h3 class="agenda-head">Section Header</h3><p class="agenda-copy">Lorem ipsum dolor sit amet, consectetur adipiscing elit. Curabitur at fringilla velit.</p></div>

  <footer class="footer">
    <svg class="layer" viewBox="0 0 534 22" preserveAspectRatio="none">
      <polygon points="0,0 424,0 434,22 0,22" fill="var(--footer)"/>
      <polygon points="424,0 432,0 444,22 434,22" fill="var(--mid-blue)"/>
    </svg>
    <p class="footer-text"><span class="page">5</span><span class="sep">|</span>Copyright © Kelvoran 2022</p>
    <div class="wordmark">Kelvoran</div>
  </footer>
</section>

<!-- Mission -->
<section class="slide slide--mission">
  <h2 class="slide-title">Our Mission</h2>
  <svg class="mission-image" viewBox="0 0 245 213" preserveAspectRatio="none" role="img" aria-label="Photo: computer hardware with liquid cooling tubes and red cables">
    <defs>
      <linearGradient id="missionPhoto" x1="0" y1="0" x2="1" y2="1">
        <stop offset="0" stop-color="#0d2a4a"/>
        <stop offset=".5" stop-color="#173d63"/>
        <stop offset="1" stop-color="#050b16"/>
      </linearGradient>
    </defs>
    <rect width="245" height="213" fill="url(#missionPhoto)"/>
  </svg>
  <p class="mission-copy">Lorem ipsum dolor sit amet, consectetur adipiscing elit. Curabitur at fringilla velit. In ac sagittis nulla. Nulla quis erat et ligula aliquam sagittis in viverra mauris. Pellentesque pharetra hendrerit orci at. Donec vel suscipit purus, ultrices ornare neque. Sed nec est a lacus lacinia venenatis non at est. Vestibulum vitae lorem lectus. Phasellus gravida mauris a sapien elementum malesuada. Vestibulum ut urna eu dolor.</p>
  <h3 class="mission-head">Section Header</h3>
  <p class="mission-copy mission-copy--second">Donec vel suscipit purus, ultrices ornare neque. Sed nec est a lacus lacinia venenatis non at est. Vestibulum vitae lorem lectus. Phasellus gravida mauris a sapien elementum malesuada. Vestibulum ut urna eu dolor.</p>
  <footer class="footer">
    <svg class="layer" viewBox="0 0 534 22" preserveAspectRatio="none">
      <polygon points="0,0 424,0 434,22 0,22" fill="var(--footer)"/>
      <polygon points="424,0 432,0 444,22 434,22" fill="var(--mid-blue)"/>
    </svg>
    <p class="footer-text"><span class="page">6</span><span class="sep">|</span>Copyright © Kelvoran 2022</p>
    <div class="wordmark">Kelvoran</div>
  </footer>
</section>

<div class="part-label">PART 1</div>

</body>
</html>
```